Business Card Design For Office Furniture Clearance Company

Kestrel Office Clearance - our company name pretty much explains what we do, we clear offices for high end clients, mainly plc's and large international companies.

We require a nice looking business card that displays professionalism but without being too serious.

It would be nice to see just a little more than a conventional boring business card, make sure you add some flare.

Industry/Entity Type

Office Furniture

Contact Information for Business Card

CARD 1

Mark Holloway
Director
mark@kestrelofficeclearance.co.uk
m: 07700 153928

t: 01632 960418
www.kestrelofficeclearance.co.uk

Kestrel Office Clearance
Unit K4 B
2-8 Fenwick Lane
Harwick
Dunmere Vale
ZZ9 4QT

free office clearances… you cant get better than that.

CARD 2

Peter Radford
Director
peter@kestrelofficeclearance.co.uk
m: 07700 382615

t: 01632 960418

Kestrel Office Clearance
Unit K4 B
2-8 Fenwick Lane
Harwick
Dunmere Vale
ZZ9 4QT

Font styles to use
Sans Serif

Requirements
Must have
• A white background - as we have a blue logo.
Nice to have
• Nice use of the logo - play around with this and dissect it.

```html
<!DOCTYPE html>
<html lang="en">
<head>
<meta charset="utf-8">
<title>Kestrel Office Clearance – Business Cards</title>
<link rel="stylesheet" href="https://fonts.googleapis.com/css2?family=Quicksand:wght@500;700&display=swap">
<style>
  :root{
    --blue:#1b7fc0;
    --blue-deep:#1f5f96;
    --white:#ffffff;
    --backdrop:#e6e9ed;
    --flame-a:rgba(250,205,185,.55);
    --flame-b:rgba(255,236,200,.25);
  }
  *{box-sizing:border-box;margin:0;padding:0}
  html,body{width:1200px;height:900px;overflow:hidden}
  body{background:var(--backdrop);font-family:"Quicksand",Arial,sans-serif;position:relative}

  .card{position:absolute;left:280px;width:640px;height:380px;background:var(--white);
        border-radius:26px;overflow:hidden;box-shadow:0 10px 28px rgba(0,0,0,.18)}
  .card--front{top:45px}
  .card--back{top:470px}

  /* front */
  .flame-art{position:absolute;left:0;bottom:0;width:250px;height:280px;
     background:radial-gradient(ellipse at 45% 70%,var(--flame-a),var(--flame-b) 55%,transparent 75%)}
  .front-brand{position:absolute;left:190px;top:70px;display:flex;align-items:center;gap:18px}
  .brand-dot{width:130px;height:130px;border-radius:50%;background:var(--blue);flex:none}
  .brand-name{color:var(--blue);font-weight:700;font-size:26px;line-height:1.15;width:200px}
  .front-web{position:absolute;left:330px;top:225px;color:var(--blue-deep);font-weight:700;font-size:14px}
  .tagline{position:absolute;left:40px;right:30px;bottom:42px;color:var(--blue);font-weight:700;
     font-size:17px;white-space:nowrap;text-align:center}

  /* back */
  .band{position:absolute;left:0;right:0;top:225px;bottom:0;background:var(--blue)}
  .holder{position:absolute;left:36px;top:150px;color:var(--blue-deep)}
  .holder__name{font-weight:700;font-size:24px;text-transform:uppercase}
  .holder__role{font-weight:700;font-size:13px;text-transform:uppercase;color:var(--blue)}
  .back-brand{position:absolute;right:34px;top:28px;display:flex;flex-direction:column;align-items:flex-end;gap:10px}
  .back-brand .brand-dot{width:120px;height:120px;margin-right:40px}
  .back-brand .brand-name{width:auto;font-size:19px;text-transform:uppercase;color:var(--blue-deep)}
  .corner-disc{position:absolute;left:20px;bottom:-70px;width:190px;height:190px;border-radius:50%;
     background:var(--white);border:3px solid var(--blue-deep)}
  .address{position:absolute;right:34px;top:236px;color:var(--white);font-weight:700;font-size:13px;
     line-height:1.3;text-align:right;font-style:normal}
  .contacts{position:absolute;left:250px;top:292px;list-style:none;color:var(--white);
     font-weight:700;font-size:15px;line-height:1.4}
  .contacts li{display:flex;align-items:center;gap:9px}
  .contacts svg{width:13px;height:13px;flex:none}
</style>
</head>
<body>

<section class="card card--front" aria-label="Card front">
  <div class="flame-art" role="img" aria-label="Faint flame illustration"></div>
  <div class="front-brand">
    <span class="brand-dot"></span>
    <span class="brand-name">Kestrel Office Clearance</span>
  </div>
  <p class="front-web">www.kestrelofficeclearance.co.uk</p>
  <p class="tagline">ZERO-COST OFFICE CLEARANCES... HARD TO BEAT THAT DEAL</p>
</section>

<section class="card card--back" aria-label="Card back">
  <div class="band"></div>
  <div class="corner-disc"></div>
  <div class="holder">
    <p class="holder__name">Mark Holloway</p>
    <p class="holder__role">Director</p>
  </div>
  <div class="back-brand">
    <span class="brand-dot"></span>
    <span class="brand-name">Kestrel Office Clearance</span>
  </div>
  <address class="address">
    Unit K4 B, 2-8 Fenwick Lane,<br>Harwick,<br>Dunmere Vale,<br>ZZ9 4QT
  </address>
  <ul class="contacts">
    <li><svg viewBox="0 0 12 12"><rect x="3" y="0.5" width="6" height="11" rx="1.2" fill="none" stroke="#fff" stroke-width="1.2"/><circle cx="6" cy="9.6" r=".7" fill="#fff"/></svg>07700 153928</li>
    <li><svg viewBox="0 0 12 12"><path d="M2.5 1l2 .3.8 2.4-1.3 1a6 6 0 0 0 3.3 3.3l1-1.3 2.4.8.3 2A1.5 1.5 0 0 1 9.5 11 8.5 8.5 0 0 1 1 2.5 1.5 1.5 0 0 1 2.5 1z" fill="#fff"/></svg>01632 960418</li>
    <li><svg viewBox="0 0 12 12"><rect x="0.8" y="2.2" width="10.4" height="7.6" rx="1" fill="none" stroke="#fff" stroke-width="1.2"/><path d="M1 2.8l5 3.8 5-3.8" fill="none" stroke="#fff" stroke-width="1.2"/></svg>mark@kestrelofficeclearance.co.uk</li>
    <li><svg viewBox="0 0 12 12"><circle cx="6" cy="6" r="5" fill="none" stroke="#fff" stroke-width="1.2"/><ellipse cx="6" cy="6" rx="2.2" ry="5" fill="none" stroke="#fff" stroke-width="1"/><path d="M1 6h10" stroke="#fff" stroke-width="1"/></svg>www.kestrelofficeclearance.co.uk</li>
  </ul>
</section>

</body>
</html>
```